Bref créative
ZARVEN Skin Care
Bright & Fun-filled
Maribel Dunstan
Owner
none on card
zarvenbodycare@plumtree-mail.com
www.zarvenbodycare-shop.com
Natural Skin Care Solutions

```html
<!DOCTYPE html>
<html lang="en">
<head>
<meta charset="utf-8">
<title>ZARVEN Skin Care – Business Card</title>
<link rel="stylesheet" href="https://fonts.googleapis.com/css2?family=Roboto+Condensed:wght@300;400;700&family=Dancing+Script:wght@500&display=swap">
<style>
  :root {
    --backdrop: #ece9e4;
    --card: #ffffff;
    --logo-grey: #8a8d8f;
    --lime: #9bc53d;
    --leaf-dark: #2f6b12;
    --leaf-mid: #5c9a22;
    --leaf-light: #a6cf4a;
    --name-green: #3d7a17;
    --text-grey: #6e7173;
    --silver: #c9ccce;
  }
  * { margin: 0; padding: 0; box-sizing: border-box; }
  html, body {
    width: 1200px; height: 897px; overflow: hidden;
    background: var(--backdrop);
  }
  .card {
    position: absolute; left: 385px; top: 74px;
    width: 430px; height: 750px;
    background: var(--card);
    border-radius: 34px;
    overflow: hidden;
    box-shadow: 0 14px 40px rgba(0,0,0,.18);
    font-family: "Roboto Condensed", Arial, sans-serif;
    text-align: center;
  }
  .brand {
    margin-top: 92px;
    font-size: 72px; font-weight: 400; letter-spacing: 2px;
    color: var(--logo-grey); line-height: 1;
  }
  .brand-rule {
    width: 210px; height: 4px; margin: 10px auto 0;
    background: var(--lime);
  }
  .tagline {
    margin-top: 14px;
    font-family: "Dancing Script", cursive;
    font-size: 25px; color: var(--name-green);
  }
  .holder-name {
    margin-top: 42px;
    font-size: 34px; font-weight: 700; color: var(--name-green);
  }
  .holder-role {
    margin-top: 2px;
    font-size: 20px; font-weight: 300; color: var(--text-grey);
  }
  .contact {
    margin-top: 22px; list-style: none;
    font-size: 15px; color: var(--text-grey); line-height: 1.5;
  }
  .contact b { color: var(--name-green); }
  .leaf-band {
    position: absolute; left: 0; bottom: 0; width: 430px; height: 250px;
  }
  .website {
    position: absolute; left: 0; right: 0; bottom: 30px;
    font-size: 17px; color: #ffffff; letter-spacing: .5px;
  }
</style>
</head>
<body>
  <article class="card">
    <div class="brand">ZARVEN</div>
    <div class="brand-rule"></div>
    <p class="tagline">Natural Skin Care Solutions</p>
    <h1 class="holder-name">Maribel Dunstan</h1>
    <p class="holder-role">Owner</p>
    <ul class="contact">
      <li><b>E:</b> zarvenbodycare@plumtree-mail.com</li>
    </ul>

    <svg class="leaf-band" viewBox="0 0 430 250" role="img" aria-label="Green leaf artwork on the card's lower band">
      <defs>
        <linearGradient id="leafGrad" x1="0" y1="0" x2="1" y2="1">
          <stop offset="0" stop-color="var(--leaf-light)"/>
          <stop offset="0.5" stop-color="var(--leaf-mid)"/>
          <stop offset="1" stop-color="var(--leaf-dark)"/>
        </linearGradient>
      </defs>
      <path d="M0 120 C120 120 300 90 430 10 L430 250 L0 250 Z" fill="var(--silver)"/>
      <path d="M0 132 C130 132 310 105 430 28 L430 250 L0 250 Z" fill="url(#leafGrad)"/>
    </svg>
    <p class="website">www.zarvenbodycare-shop.com</p>
  </article>
</body>
</html>
```